Business Cards - Brightpath Horizon

need to design unique business card for my mortgage business. I need to design credit card style business card for my business or any unique idea that you might have

Target Market(s)

Home Loan customers

Industry/Entity Type

Mortgage Brokerage

Contact Information for Business Card

please design credit card style or very unique style business card

Colors

Designer to choose colors to be used in the design.

Requirements
Must have
• Name
• position
• Phone number
• fax number
• email address
• website address
• social media address
• All above fields will be provided once design in finalised

```html
<!DOCTYPE html>
<html lang="en">
<head>
<meta charset="utf-8">
<title>Brightpath Horizon – Business Card</title>
<link rel="stylesheet" href="https://fonts.googleapis.com/css2?family=Noto+Serif:wght@400;700&display=swap">
<style>
  :root {
    --bg: #1f1f1f;
    --brand-blue: #0a2fc4;
    --brand-blue-light: #7c91e2;
    --accent-orange: #f08a1c;
    --text-grey: #4a4a4a;
    --card-white: #ffffff;
    --card-shade: #cfcfcf;
  }
  * { box-sizing: border-box; margin: 0; padding: 0; }
  html, body { width: 1200px; height: 960px; overflow: hidden; background: var(--bg); }
  body { position: relative; font-family: "Noto Serif", serif; }

  .card {
    position: absolute;
    width: 600px;
    height: 342px;
    border-radius: 22px;
    box-shadow: 0 3px 6px rgba(0,0,0,0.6);
  }
  .card--front {
    left: 314px; top: 113px;
    background: linear-gradient(125deg, var(--card-white) 55%, var(--card-shade) 100%);
    color: var(--brand-blue);
  }
  .card--back {
    left: 311px; top: 472px;
    background: linear-gradient(115deg, var(--brand-blue-light) 0%, var(--brand-blue) 48%, var(--brand-blue) 100%);
    color: #fff;
  }

  .holder { position: absolute; left: 39px; top: 44px; }
  .holder__name { font-size: 21px; font-weight: 400; letter-spacing: 0.5px; line-height: 1.1; }
  .holder__role { font-size: 15px; color: var(--accent-orange); line-height: 1.2; }

  .brand {
    position: absolute; right: 40px; top: 62px;
    display: flex; align-items: center; gap: 12px;
  }
  .brand__mark { width: 18px; height: 18px; border-radius: 50%; background: var(--accent-orange); }
  .brand__name { font-size: 30px; line-height: 1.05; color: var(--brand-blue); text-align: right; }

  .phone-main { position: absolute; left: 38px; top: 182px; font-size: 48px; line-height: 1; }

  .contacts { position: absolute; left: 38px; top: 255px; font-size: 14px; line-height: 19px; color: var(--text-grey); list-style: none; }
  .contacts__label { color: var(--brand-blue); font-weight: 700; margin-right: 3px; }

  .address { position: absolute; right: 38px; top: 274px; font-size: 14px; line-height: 19px; color: var(--text-grey); text-align: right; font-style: normal; }

  .back-brand {
    position: absolute; left: 0; right: 0; top: 122px;
    display: flex; justify-content: center; align-items: center; gap: 16px;
  }
  .back-brand__mark { width: 22px; height: 22px; border-radius: 50%; background: #fff; }
  .back-brand__name { font-size: 42px; line-height: 1.05; text-align: center; }

  .social { position: absolute; left: 0; right: 0; top: 280px; display: flex; justify-content: center; gap: 3px; list-style: none; }
  .social__badge { width: 27px; height: 27px; border-radius: 50%; background: #fff; }
</style>
</head>
<body>
  <section class="card card--front" aria-label="Card front">
    <div class="holder">
      <div class="holder__name">DANIEL REYES</div>
      <div class="holder__role">CEO/FOUNDER</div>
    </div>
    <div class="brand">
      <span class="brand__mark"></span>
      <span class="brand__name">Brightpath<br>Horizon</span>
    </div>
    <div class="phone-main">555 210 4816</div>
    <ul class="contacts">
      <li><span class="contacts__label">P:</span>555 372 9041</li>
      <li><span class="contacts__label">E:</span>mail@brightpath.com</li>
      <li><span class="contacts__label">W:</span>www.brightpath.com</li>
    </ul>
    <address class="address">1420 Juniper Court<br>Fairbanks, Alaska 99701</address>
  </section>

  <section class="card card--back" aria-label="Card back">
    <div class="back-brand">
      <span class="back-brand__mark"></span>
      <span class="back-brand__name">Brightpath Horizon</span>
    </div>
    <ul class="social" aria-label="Social media links">
      <li class="social__badge"></li>
      <li class="social__badge"></li>
      <li class="social__badge"></li>
      <li class="social__badge"></li>
    </ul>
  </section>
</body>
</html>
```